Brisbane IT support business needs our first website

Hi All,

We are after a new website design for our IT solutions and support business.The business name is Harbourline Computing Services Group, or HCSG for short. We provide a range of solutions and services within the IT space.

I would like to utilize the two colours in our business logo I have uploaded.

I understand this is initially for the design only aspect of the site, but I would like to engage the winner to finish coding the website and finalize after also.

Target Market(s)

Other businesses owners and home users.

Industry/Entity Type

Business

Requirements
Must have
• Nice clean and functional design utilizing our business colours from the logo.

```html
<!DOCTYPE html>
<html lang="en">
<head>
<meta charset="utf-8">
<title>Harbourline Computing Services Group</title>
<link href="https://fonts.googleapis.com/css2?family=Lato:wght@300;400;700;900&display=swap" rel="stylesheet">
<style>
:root{
  --orange:#e8781e;
  --orange-dark:#d0661a;
  --navy:#0e4660;
  --navy-deep:#0b3a50;
  --ink:#333a40;
  --muted:#7b848b;
  --light:#f1f2f3;
  --footer:#2e3338;
  --footer-deep:#24282c;
  --white:#ffffff;
}
*{margin:0;padding:0;box-sizing:border-box}
html,body{width:1200px;height:2688px;overflow:hidden}
body{font-family:"Lato",Arial,sans-serif;color:var(--ink);background:var(--white)}
section,header,footer{position:relative;width:1200px;overflow:hidden}

/* Header */
.site-header{height:120px;background:var(--white);display:flex;align-items:flex-start;padding:0 40px}
.brand{display:flex;align-items:center;gap:14px;margin-top:18px}
.brand-mark{width:72px;height:72px;border-radius:50%;background:var(--navy)}
.brand-name{font-size:48px;font-weight:900;color:var(--orange);letter-spacing:1px}
.main-nav{display:flex;margin-left:84px;margin-top:58px}
.main-nav a{font-size:17px;color:var(--ink);text-decoration:none;padding:18px 20px;font-weight:700}
.main-nav a.active{background:var(--orange);color:var(--white);margin-top:-58px;padding-top:76px}
.header-contact{position:absolute;right:40px;top:20px;display:flex;gap:30px;font-size:16px;color:var(--ink)}
.header-contact span{display:flex;align-items:center;gap:8px}

/* Hero */
.hero{height:440px;background:linear-gradient(100deg,#0b0f14 0%,#1c2a36 45%,#6a4a2a 80%,#2b2118 100%)}
.hero-visual{position:absolute;right:0;top:0;width:640px;height:440px;background:radial-gradient(circle at 60% 55%,#c9a37a 0%,#6d5542 25%,rgba(20,28,36,0) 60%)}
.hero-copy{position:absolute;left:148px;top:90px;width:460px}
.hero-copy h1{font-size:62px;font-weight:900;color:var(--white);line-height:1}
.hero-copy h2{font-size:52px;font-weight:400;color:var(--orange);margin-top:8px}
.hero-copy p{font-size:17px;color:#e4e6e8;line-height:1.45;margin-top:18px}
.btn{display:inline-block;background:var(--orange);color:var(--white);font-size:18px;font-weight:700;padding:14px 28px;text-decoration:none}
.hero-copy .btn{margin-top:26px}

/* About */
.about{height:290px;background:var(--light);text-align:center;padding-top:52px}
.section-title{font-size:46px;font-weight:400;color:var(--navy)}
.section-title em{font-style:normal;color:var(--orange)}
.section-sub{font-size:19px;color:var(--orange);margin-top:6px}
.about p{width:1000px;margin:24px auto 0;font-size:16px;line-height:1.55;color:var(--muted)}

/* Services */
.services{height:510px;text-align:center;padding-top:66px}
.services .section-sub{color:var(--ink)}
.service-grid{display:grid;grid-template-columns:440px 440px;column-gap:70px;row-gap:60px;justify-content:center;margin-top:50px;text-align:left}
.service{display:flex;gap:24px}
.service-icon{flex:0 0 96px;height:96px;border-radius:50%;background:var(--navy);display:flex;align-items:center;justify-content:center}
.service h3{font-size:24px;font-weight:700;color:var(--orange);margin-top:6px}
.service p{font-size:15px;line-height:1.5;color:var(--muted);margin-top:6px}

/* Portfolio */
.portfolio{height:400px;background:var(--navy);text-align:center;padding-top:46px;color:var(--white)}
.portfolio .section-title{color:var(--white)}
.portfolio .section-sub{color:#cfe0e8;font-size:17px}
.portfolio-item{position:absolute;left:200px;top:150px;display:flex;gap:44px;text-align:left}
.portfolio-image{width:390px;height:210px;background:linear-gradient(135deg,#8ea6b5,#3e5a6c)}
.portfolio-body{width:440px;padding-top:10px}
.portfolio-body h3{font-size:28px;font-weight:700;display:flex;align-items:center;gap:12px}
.portfolio-body p{font-size:16px;line-height:1.5;color:#d6e3ea;margin-top:14px}
.btn-outline{display:inline-block;border:2px solid var(--white);color:var(--white);font-size:16px;padding:9px 20px;margin-top:20px;text-decoration:none}
.slider-arrow{position:absolute;top:270px}
.slider-arrow.prev{left:136px}
.slider-arrow.next{right:136px}

/* Partners */
.partners{height:320px;text-align:center;padding-top:40px}
.partners .section-sub{font-size:17px}
.partner-grid{display:grid;grid-template-columns:repeat(4,190px);column-gap:70px;row-gap:40px;justify-content:center;margin-top:34px}
.partner-badge{height:64px;background:#cfd3d6;border-radius:4px}

/* Call to action */
.cta{height:312px;background:var(--orange);text-align:center;color:var(--white);padding-top:52px}
.cta h2{font-size:44px;font-weight:400}
.cta .tagline{font-size:18px;margin-top:8px}
.cta p{width:820px;margin:20px auto 0;font-size:15px;line-height:1.55;color:#fff3e8}
.cta .btn-outline{margin-top:22px}

/* Footer */
.site-footer{height:248px;background:var(--footer);color:#dfe2e4}
.footer-contact{position:absolute;left:128px;top:36px}
.footer-contact h2{font-size:30px;font-weight:400;color:var(--white)}
.footer-contact ul{list-style:none;margin-top:16px}
.footer-contact li{display:flex;align-items:center;gap:12px;font-size:15px;line-height:1.3;margin-bottom:12px}
.footer-contact li strong{color:var(--orange);font-weight:700}
.footer-map{position:absolute;left:620px;top:32px;width:440px;height:150px;background:linear-gradient(135deg,#e8e4da,#cfd8c8)}
.map-link{position:absolute;left:620px;top:196px;font-size:14px;color:var(--white)}
.bottom-bar{height:48px;background:var(--footer-deep);display:flex;align-items:center;justify-content:space-between;padding:0 128px;font-size:13px;color:#a9afb4}
.social{display:flex;gap:8px}
.social span{width:24px;height:24px;border-radius:50%;background:var(--orange)}
</style>
</head>
<body>

<header class="site-header">
  <div class="brand">
    <span class="brand-mark"></span>
    <span class="brand-name">HCSG</span>
  </div>
  <nav class="main-nav">
    <a class="active" href="#">Home</a>
    <a href="#">About Us</a>
    <a href="#">Services</a>
    <a href="#">Technology</a>
    <a href="#">Solutions</a>
    <a href="#">Support</a>
    <a href="#">Contact</a>
  </nav>
  <div class="header-contact">
    <span><svg width="18" height="18" viewBox="0 0 24 24"><path fill="#0e4660" d="M6.6 10.8a15 15 0 0 0 6.6 6.6l2.2-2.2c.3-.3.7-.4 1-.2 1.1.4 2.3.6 3.6.6.6 0 1 .4 1 1V20c0 .6-.4 1-1 1A17 17 0 0 1 3 4c0-.6.4-1 1-1h3.5c.6 0 1 .4 1 1 0 1.3.2 2.5.6 3.6.1.3 0 .7-.2 1z"/></svg>Call us (07) 3000 4821</span>
    <span><svg width="18" height="14" viewBox="0 0 24 18"><rect x="1" y="1" width="22" height="16" fill="none" stroke="#0e4660" stroke-width="2"/><path d="M1 1l11 9 11-9" fill="none" stroke="#0e4660" stroke-width="2"/></svg>Email: hello@hcsg.net</span>
  </div>
</header>

<section class="hero">
  <div class="hero-visual" role="img" aria-label="Businessman's open hand holding glowing cloud and technology icons"></div>
  <div class="hero-copy">
    <h1>SUCCESS WITH</h1>
    <h2>Our Creative Solutions</h2>
    <p>We keep your business systems running smoothly with fast, friendly local support and clever solutions built around you.</p>
    <a class="btn" href="#">Learn More</a>
  </div>
</section>

<section class="about">
  <h2 class="section-title">About <em>HCSG</em></h2>
  <div class="section-sub">Local experts in business and home technology support.</div>
  <p>Harbourline Computing Services Group helps local businesses and home users get the most from their technology. From everyday support to network design, our team delivers practical, reliable solutions with honest advice and no jargon. We take time to understand how you work, then build systems that keep you productive, secure and ready to grow. Whether you need a quick fix or a long term partner, we are here to help.</p>
</section>

<section class="services">
  <h2 class="section-title"><em>Our</em> Services</h2>
  <div class="section-sub">Providing the best quality services</div>
  <div class="service-grid">
    <div class="service">
      <div class="service-icon"><svg width="46" height="46" viewBox="0 0 24 24"><path fill="#fff" d="M22 6.5a5.5 5.5 0 0 1-7.4 5.2L6 20.3a2 2 0 0 1-2.8-2.8l8.6-8.6A5.5 5.5 0 0 1 17.5 1.5l-3 3 .6 3.4 3.4.6 3-3c.3.6.5 1.3.5 2z"/></svg></div>
      <div><h3>IT Support</h3><p>Fast help desk and on site support for your staff, computers and printers, with friendly technicians who explain every step.</p></div>
    </div>
    <div class="service">
      <div class="service-icon"><svg width="40" height="46" viewBox="0 0 20 24"><ellipse cx="10" cy="4" rx="9" ry="3.2" fill="#fff"/><path fill="#fff" d="M1 6.5c2 2.4 16 2.4 18 0V11c-2 2.4-16 2.4-18 0zM1 13.5c2 2.4 16 2.4 18 0V18c-2 2.4-16 2.4-18 0z"/></svg></div>
      <div><h3>Data Management</h3><p>Secure backup, storage and recovery plans that protect your important files and keep your business information organised and safe.</p></div>
    </div>
    <div class="service">
      <div class="service-icon"><svg width="46" height="42" viewBox="0 0 24 22"><path d="M2 1v19h21" fill="none" stroke="#fff" stroke-width="2"/><path d="M5 16l5-6 4 3 7-8" fill="none" stroke="#fff" stroke-width="2.2"/></svg></div>
      <div><h3>Fast Results</h3><p>Quick response times and clear fixes that get you back to work sooner, with minimal disruption to your day.</p></div>
    </div>
    <div class="service">
      <div class="service-icon"><svg width="36" height="46" viewBox="0 0 18 24"><path d="M4 10V7a5 5 0 0 1 10 0v3" fill="none" stroke="#fff" stroke-width="2.4"/><rect x="1" y="10" width="16" height="13" rx="1.5" fill="#fff"/></svg></div>
      <div><h3>100% Secure</h3><p>Firewalls, antivirus and monitoring that guard your network around the clock against threats, leaks and unwanted access.</p></div>
    </div>
  </div>
</section>

<section class="portfolio">
  <h2 class="section-title">Our Work Portfolio</h2>
  <div class="section-sub">We deliver top quality products</div>
  <svg class="slider-arrow prev" width="18" height="36" viewBox="0 0 18 36"><path d="M16 2L2 18l14 16" fill="none" stroke="#fff" stroke-width="3"/></svg>
  <div class="portfolio-item">
    <div class="portfolio-image" role="img" aria-label="Hand holding a tablet with cloud and device icons above it"></div>
    <div class="portfolio-body">
      <h3><svg width="40" height="26" viewBox="0 0 40 26"><path fill="#fff" d="M10 26a9 9 0 0 1-1-18 12 12 0 0 1 23 3 7.5 7.5 0 0 1-1 15z"/></svg>Project Name</h3>
      <p>A complete network and cloud upgrade for a growing local firm, delivering faster systems, safer data and happier staff across three offices.</p>
      <a class="btn-outline" href="#">View Project</a>
    </div>
  </div>
  <svg class="slider-arrow next" width="18" height="36" viewBox="0 0 18 36"><path d="M2 2l14 16L2 34" fill="none" stroke="#fff" stroke-width="3"/></svg>
</section>

<section class="partners">
  <h2 class="section-title"><em>Our</em> Partners</h2>
  <div class="section-sub">Trusted by leading local businesses</div>
  <div class="partner-grid">
    <div class="partner-badge"></div><div class="partner-badge"></div><div class="partner-badge"></div><div class="partner-badge"></div>
    <div class="partner-badge"></div><div class="partner-badge"></div><div class="partner-badge"></div><div class="partner-badge"></div>
  </div>
</section>

<section class="cta">
  <h2>We Can Help Build Your Project</h2>
  <div class="tagline">Tell Us About Your Project</div>
  <p>Whether you are a small office or a busy household, our team can plan, install and support the technology you need. Get in touch today for a free, no obligation chat about your goals.</p>
  <a class="btn-outline" href="#">Contact us &#9993;</a>
</section>

<footer class="site-footer">
  <div class="footer-contact">
    <h2>Contact Info</h2>
    <ul>
      <li><svg width="16" height="22" viewBox="0 0 16 22"><path fill="#e8781e" d="M8 0a8 8 0 0 1 8 8c0 6-8 14-8 14S0 14 0 8a8 8 0 0 1 8-8zm0 5a3 3 0 1 0 0 6 3 3 0 0 0 0-6z"/></svg><span><strong>Harbourline Computing Services Group</strong><br>12 Quayside Lane, Brisbane QLD</span></li>
      <li><svg width="16" height="16" viewBox="0 0 24 24"><path fill="#e8781e" d="M6.6 10.8a15 15 0 0 0 6.6 6.6l2.2-2.2c.3-.3.7-.4 1-.2 1.1.4 2.3.6 3.6.6.6 0 1 .4 1 1V20c0 .6-.4 1-1 1A17 17 0 0 1 3 4c0-.6.4-1 1-1h3.5c.6 0 1 .4 1 1 0 1.3.2 2.5.6 3.6.1.3 0 .7-.2 1z"/></svg>(07) 3000 4821</li>
      <li><svg width="16" height="12" viewBox="0 0 24 18"><rect x="1" y="1" width="22" height="16" fill="none" stroke="#e8781e" stroke-width="2"/><path d="M1 1l11 9 11-9" fill="none" stroke="#e8781e" stroke-width="2"/></svg>hello@hcsg.net</li>
    </ul>
  </div>
  <div class="footer-map" role="img" aria-label="Street map showing the office location"></div>
  <a class="map-link" href="#">View Full Map &rarr;</a>
</footer>
<div class="bottom-bar">
  <div class="social"><span></span><span></span><span></span><span></span></div>
  <div>&copy; 2014 Harbourline Computing Services Group. All Rights Reserved.</div>
</div>

</body>
</html>
```